Real Estate Website

Please refer to the attached document. It will be for a real estate agency specialising in commercial and residential sales. looking for Modern and minimalist, Sleek, professional, premium feel

```html
<!DOCTYPE html>
<html lang="en">
<head>
<meta charset="utf-8">
<title>Varenna Group – Commercial &amp; Residential Property</title>
<link href="https://fonts.googleapis.com/css2?family=Poppins:wght@300;400;500;600;700&display=swap" rel="stylesheet">
<style>
:root{
  --orange:#f26b40;
  --orange-soft:#fde3d9;
  --navy:#263746;
  --navy-deep:#1f2e3b;
  --ink:#1f2a33;
  --muted:#6b7278;
  --line:#e3e5e8;
  --grey-bg:#f4f4f4;
  --white:#ffffff;
}
*{margin:0;padding:0;box-sizing:border-box}
html,body{width:1200px;height:5021px;overflow:hidden}
body{font-family:"Poppins",sans-serif;color:var(--ink);background:var(--white);position:relative}
.abs{position:absolute}
.accent{color:var(--orange)}
.label{font-size:13px;font-weight:600;letter-spacing:.3px;text-transform:uppercase;display:flex;align-items:center;gap:8px;color:var(--ink)}
.pin{width:14px;height:16px;display:inline-block}
.heading{font-size:25px;font-weight:600;color:var(--ink)}
.body-text{font-size:12.5px;line-height:23px;color:var(--muted)}
.btn{display:inline-flex;align-items:center;justify-content:center;gap:8px;font-size:13.5px;font-weight:500;color:#fff;border-radius:4px}
.btn-orange{background:var(--orange)}
.btn-navy{background:var(--navy)}
.btn svg{width:12px;height:12px}

/* header */
.topbar{top:0;left:560px;width:640px;height:28px}
.topbar-info{top:4px;right:0;width:640px;height:20px;font-size:11px;color:#fff;display:flex;align-items:center}
.brand{display:flex;align-items:center;gap:9px}
.brand-dot{width:24px;height:24px;border-radius:50%;background:var(--orange)}
.brand-name{font-size:24px;font-weight:700;color:var(--ink);line-height:1}
.nav{top:47px;left:398px;display:flex;gap:33px;font-size:12.5px;color:#3d454c;white-space:nowrap}
.nav .active{color:var(--orange)}

/* hero */
.hero{top:84px;left:0;width:1200px;height:578px;background:linear-gradient(100deg,#1b3446 0%,#2b4c63 45%,#6b8596 75%,#a37f5e 100%)}
.hero-title{left:142px;top:72px;color:#fff;font-size:34px;line-height:54px;font-weight:700;letter-spacing:.5px}
.hero-title .light{font-weight:300}
.hero-sub{left:142px;top:310px;border-left:2px solid rgba(255,255,255,.7);padding-left:14px;color:#fff;font-size:13.5px;line-height:24px;width:420px}
.hero-btn{left:142px;top:428px;width:204px;height:46px;border-radius:24px}

/* cards */
.card{background:#fff;border:1px solid var(--line);border-radius:4px;box-shadow:0 2px 10px rgba(0,0,0,.05)}
.card-img{height:164px}
.card-body{padding:20px 14px}
.card-title{font-size:14.5px;font-weight:600;margin-bottom:10px}
.learn{margin-top:22px;font-size:12.5px;font-weight:500;text-decoration:underline;display:flex;align-items:center;gap:10px}

/* features */
.feature h4{font-size:15px;font-weight:600;margin-bottom:8px}
.feature p{font-size:12px;line-height:21px;color:var(--muted)}
.icon-circle{width:58px;height:58px;border-radius:50%;display:flex;align-items:center;justify-content:center}
.icon-circle svg{width:26px;height:26px}

/* testimonials */
.quote{width:36px;height:36px;border-radius:50%;background:var(--navy);color:#fff;font-size:30px;font-weight:700;line-height:46px;text-align:center;position:absolute;top:-14px;left:20px}
.quote.o{background:var(--orange)}
.stars{color:#f5b400;font-size:18px;letter-spacing:2px}
.badge{width:22px;height:22px;border-radius:50%;border:3px solid #d9dde1}

/* form */
.field{position:absolute;height:47px;border:1px solid #d7dade;border-radius:3px;display:flex;align-items:center;font-size:12.5px;color:#8a9096}
.field .ic{width:48px;display:flex;justify-content:center;border-right:1px solid #d7dade;height:22px;align-items:center;margin-right:14px}
.field svg{width:14px;height:14px;stroke:#9aa0a6;fill:none;stroke-width:1.6}

/* footer */
.foot-h{font-size:14.5px;font-weight:600;color:#fff}
.foot-bar{width:26px;height:2px;background:var(--orange);margin:10px 0 16px}
.foot-list{list-style:none;font-size:12.5px;line-height:29px;color:#dfe4e8}
.foot-list li::before{content:"› ";color:var(--orange)}
</style>
</head>
<body>

<!-- top contact strip -->
<svg class="abs topbar" viewBox="0 0 640 28" aria-hidden="true">
  <polygon points="30,0 330,0 315,28 15,28" fill="var(--navy)"/>
  <polygon points="338,0 640,0 640,28 323,28" fill="var(--orange)"/>
</svg>
<div class="abs topbar-info">
  <span style="display:flex;gap:10px;margin-left:40px">
    <span style="width:9px;height:9px;border-radius:50%;background:#fff;display:inline-block"></span>
    <span style="width:9px;height:9px;border-radius:50%;background:#fff;display:inline-block"></span>
    <span style="width:9px;height:9px;border-radius:50%;background:#fff;display:inline-block"></span>
  </span>
  <span style="margin-left:22px">✉&nbsp; info@varennagroup.com.au</span>
  <span style="margin-left:auto;margin-right:115px;font-weight:600">☎&nbsp; (555) 014 2298</span>
</div>

<header>
  <div class="abs brand" style="top:22px;left:146px">
    <span class="brand-dot"></span>
    <span class="brand-name">Varenna Group</span>
  </div>
  <nav class="abs nav">
    <span class="active">Home</span><span>Commercial / Industrial</span><span>Residential</span><span>Business Sales</span><span>About Us</span><span>Info ⌄</span><span>Contact us</span>
  </nav>
</header>

<!-- hero -->
<section class="abs hero" role="img" aria-label="Harbour city skyline at sunset with an opera house on the waterfront">
  <div class="abs hero-title"><span class="light">SPECIALISTS IN</span><br>COMMERCIAL &amp; INDUSTRIAL<br>PROPERTY TRUSTED IN<br>RESIDENTIAL PROPERTY</div>
  <div class="abs hero-sub">Maximising Returns, Protecting Investments, Delivering Expert Property Advisory.</div>
  <div class="abs btn btn-orange hero-btn">Book an Appraisal <svg viewBox="0 0 12 12"><path d="M2 10L10 2M4 2h6v6" stroke="#fff" stroke-width="1.6" fill="none"/></svg></div>
  <svg class="abs" style="left:540px;top:532px" width="120" height="48" viewBox="0 0 120 48"><path d="M0 48C30 48 38 6 60 6S90 48 120 48Z" fill="#fff"/><path d="M54 26l6 6 6-6M54 32l6 6 6-6" stroke="var(--orange)" stroke-width="1.6" fill="none"/></svg>
</section>

<!-- appraisal -->
<section>
  <div class="abs" style="left:177px;top:780px;width:343px;height:301px;border:1.5px solid var(--orange)"></div>
  <div class="abs" role="img" aria-label="Hands reviewing architectural plans on a desk" style="left:0;top:793px;width:506px;height:458px;background:linear-gradient(135deg,#d8d3c8,#2c3038 70%)"></div>
  <div class="abs" style="left:308px;top:1072px;width:26px;height:26px;border-radius:50%;background:var(--orange);border:3px solid #fff"></div>
  <div class="abs" role="img" aria-label="Business partners shaking hands in an office" style="left:316px;top:1095px;width:237px;height:199px;border:8px solid #fff;box-shadow:0 4px 14px rgba(0,0,0,.15);background:linear-gradient(135deg,#c9cdd2,#7d848c)"></div>
  <div class="abs" style="left:602px;top:812px;width:470px">
    <div class="label"><svg class="pin" viewBox="0 0 14 16"><circle cx="7" cy="6" r="5" fill="none" stroke="var(--orange)" stroke-width="2"/><path d="M7 16l-3-5h6z" fill="var(--orange)"/></svg>Book An Appraisal</div>
    <div class="heading" style="margin-top:10px;white-space:nowrap">Discover The Real Value Of <span class="accent">Your Property</span></div>
    <p class="body-text" style="margin-top:14px">At Varenna Group, we don't just provide standard appraisals — we deliver strategic, insight-driven reports that uncover the true drivers of your property's worth. Whether it's commercial, industrial, or residential, our expertise ensures you see the full picture.</p>
    <p class="body-text" style="margin-top:9px">From market trends and rental potential to investment performance and future growth opportunities, our tailored reports give you clarity, confidence, and actionable insights.</p>
    <p class="body-text" style="margin-top:9px">Book a confidential consultation today and gain the expert guidance you need to maximise returns and make smarter property decisions.</p>
    <div class="btn btn-navy" style="margin-top:22px;width:205px;height:40px;font-size:12.5px">Schedule Consultation <svg viewBox="0 0 12 12"><path d="M2 10L10 2M4 2h6v6" stroke="#fff" stroke-width="1.6" fill="none"/></svg></div>
  </div>
  <div class="abs" role="img" aria-label="Faint line sketch of city buildings" style="left:770px;top:1170px;width:400px;height:180px;background:linear-gradient(180deg,#fff,#f3f3f3)"></div>
</section>

<!-- services -->
<section class="abs" style="top:1383px;left:0;width:1200px;height:643px;background:var(--grey-bg)">
  <div class="label abs" style="top:110px;left:0;width:1200px;justify-content:center"><svg class="pin" viewBox="0 0 14 16"><circle cx="7" cy="6" r="5" fill="none" stroke="var(--orange)" stroke-width="2"/><path d="M7 16l-3-5h6z" fill="var(--orange)"/></svg>What We Do</div>
  <div class="heading abs" style="top:136px;left:0;width:1200px;text-align:center">Property Management, <span class="accent">Sales &amp; Leasing</span></div>
  <div class="card abs" style="left:140px;top:201px;width:284px;height:350px">
    <div class="card-img" role="img" aria-label="Modern glass office buildings" style="background:linear-gradient(160deg,#5f88b5,#c9ced3)"></div>
    <div class="card-body"><div class="card-title">Commercial &amp; Industrial</div><p class="body-text" style="font-size:12px;line-height:21px">Specialist management and leasing of premium commercial and industrial assets, trusted by investors and developers.</p><div class="learn">Learn More <span class="accent">⟶</span></div></div>
  </div>
  <div class="card abs" style="left:458px;top:201px;width:284px;height:350px">
    <div class="card-img" role="img" aria-label="Brick family home with front lawn" style="background:linear-gradient(180deg,#8fb8e0,#8a5a44 60%,#4f7a3a)"></div>
    <div class="card-body"><div class="card-title">Residential Property</div><p class="body-text" style="font-size:12px;line-height:21px">Expert residential property management and sales services with proven results and exceptional client outcomes.</p><div class="learn">Learn More <span class="accent">⟶</span></div></div>
  </div>
  <div class="card abs" style="left:776px;top:201px;width:284px;height:350px">
    <div class="card-img" role="img" aria-label="Advisors meeting around a laptop" style="background:linear-gradient(160deg,#cfc6bb,#4a4f58)"></div>
    <div class="card-body"><div class="card-title">Property Advisory</div><p class="body-text" style="font-size:12px;line-height:21px">Comprehensive financial reporting, budgeting, and expense management to optimize cash flow and returns.</p><div class="learn">Learn More <span class="accent">⟶</span></div></div>
  </div>
</section>

<!-- why choose us -->
<section>
  <div class="label abs" style="top:2134px;left:0;width:1200px;justify-content:center"><svg class="pin" viewBox="0 0 14 16"><circle cx="7" cy="6" r="5" fill="none" stroke="var(--orange)" stroke-width="2"/><path d="M7 16l-3-5h6z" fill="var(--orange)"/></svg>Why Choose Us</div>
  <div class="heading abs" style="top:2160px;left:0;width:1200px;text-align:center">Commercial &amp; Industrial Property <span class="accent">Management &amp; Leasing</span></div>

  <div class="abs" style="left:478px;top:2239px;width:244px;height:244px;border-radius:50%;background:#fff;box-shadow:0 4px 24px rgba(0,0,0,.08)"></div>
  <div class="abs" style="left:487px;top:2248px;width:226px;height:226px;border-radius:50%;border:2px dashed var(--navy)"></div>
  <div class="abs" style="left:478px;top:2316px;width:244px;text-align:center">
    <div style="width:40px;height:40px;border-radius:50%;background:var(--orange);margin:0 auto 10px"></div>
    <div style="font-size:30px;font-weight:700;color:var(--ink);line-height:1">Varenna</div>
    <div style="font-size:30px;font-weight:700;color:var(--ink);line-height:1.1">Group</div>
  </div>

  <div class="feature abs" style="left:140px;top:2246px;width:240px;text-align:right"><h4>Sector Expertise</h4><p>Deep knowledge across medical, healthcare, franchise, retail, and industrial sectors, enabling tailored strategies for each asset class.</p></div>
  <div class="icon-circle abs" style="left:399px;top:2250px;background:var(--orange)"><svg viewBox="0 0 26 26"><circle cx="13" cy="13" r="10" fill="none" stroke="#fff" stroke-width="1.6"/><path d="M13 7l1.8 3.8 4.1.5-3 2.8.8 4.1L13 16.2 9.3 18.2l.8-4.1-3-2.8 4.1-.5z" fill="none" stroke="#fff" stroke-width="1.4"/></svg></div>

  <div class="feature abs" style="left:140px;top:2410px;width:240px;text-align:right"><h4>Proactive Asset Management</h4><p>Beyond operations, we actively enhance value, mitigate risk, and secure the right tenants.</p></div>
  <div class="icon-circle abs" style="left:399px;top:2414px;background:var(--navy)"><svg viewBox="0 0 26 26"><path d="M4 14l5-5 4 3 4-4 5 5-8 8z" fill="none" stroke="#fff" stroke-width="1.6"/></svg></div>

  <div class="icon-circle abs" style="left:744px;top:2250px;background:var(--navy)"><svg viewBox="0 0 26 26"><circle cx="13" cy="13" r="4" fill="none" stroke="#fff" stroke-width="1.6"/><circle cx="13" cy="13" r="9" fill="none" stroke="#fff" stroke-width="1.6" stroke-dasharray="3 2"/></svg></div>
  <div class="feature abs" style="left:820px;top:2246px;width:240px"><h4>Bespoke Solutions</h4><p>Every property is unique. We craft customised management and leasing strategies aligned with your objectives and market conditions.</p></div>

  <div class="icon-circle abs" style="left:744px;top:2414px;background:var(--orange)"><svg viewBox="0 0 26 26"><path d="M5 12h4v9H5zM9 12l4-7c2 0 2 2 1.5 4H20c1 0 2 1 1.6 2l-1.8 8c-.2.8-.9 1-1.6 1H9" fill="none" stroke="#fff" stroke-width="1.6"/></svg></div>
  <div class="feature abs" style="left:820px;top:2410px;width:240px"><h4>Professional Excellence</h4><p>Integrity, precision, and industry-leading best</p></div>

  <div class="abs btn btn-orange" style="left:497px;top:2540px;width:205px;height:43px">Book an Appraisal <svg viewBox="0 0 12 12"><path d="M2 10L10 2M4 2h6v6" stroke="#fff" stroke-width="1.6" fill="none"/></svg></div>
</section>

<!-- who we are -->
<section class="abs" style="top:2708px;left:0;width:1200px;height:487px;background:var(--grey-bg)">
  <div class="abs" style="left:144px;top:78px;width:460px">
    <div class="label"><svg class="pin" viewBox="0 0 14 16"><circle cx="7" cy="6" r="5" fill="none" stroke="var(--orange)" stroke-width="2"/><path d="M7 16l-3-5h6z" fill="var(--orange)"/></svg>Who We Are</div>
    <div class="heading" style="margin-top:10px">We Are Recognised As <span class="accent">A Trusted</span></div>
    <p class="body-text" style="margin-top:14px">At Varenna Group, we are recognised as a trusted authority in commercial and residential property management, sales, and leasing. Property owners, investors, and developers turn to us for our proven expertise, discretion, and consistent results.</p>
    <p class="body-text" style="margin-top:12px">Our mission is to set the standard for excellence in property services. Guided by innovation, integrity, and strategic execution, we deliver outcomes that protect assets, maximise returns, and create enduring value for our clients.</p>
    <div class="btn btn-navy" style="margin-top:28px;width:205px;height:41px;font-size:12.5px">Schedule Consultation <svg viewBox="0 0 12 12"><path d="M2 10L10 2M4 2h6v6" stroke="#fff" stroke-width="1.6" fill="none"/></svg></div>
  </div>
  <div class="abs" role="img" aria-label="Team meeting in a bright office with a presenter standing" style="left:643px;top:74px;width:413px;height:343px;border-radius:8px;background:linear-gradient(135deg,#d7dde3,#9aa4ad 60%,#3e4852)"></div>
</section>

<!-- testimonials -->
<section>
  <div class="label abs" style="top:3310px;left:0;width:1200px;justify-content:center"><svg class="pin" viewBox="0 0 14 16"><circle cx="7" cy="6" r="5" fill="none" stroke="var(--orange)" stroke-width="2"/><path d="M7 16l-3-5h6z" fill="var(--orange)"/></svg>Testimonials</div>
  <div class="heading abs" style="top:3336px;left:0;width:1200px;text-align:center">What Our Clients Say <span class="accent">About Us</span></div>

  <div class="card abs" style="left:140px;top:3419px;width:284px;height:282px;padding:36px 20px 0">
    <span class="quote">“</span>
    <div style="display:flex;justify-content:space-between;align-items:center"><span class="stars">★★★★★</span><span class="badge"></span></div>
    <p class="body-text" style="margin-top:14px;color:#3d454c;font-size:12px;line-height:22px">"Sed ut perspiciatis unde omnis iste natus error sit voluptatem accusantium laudantium, totam rem aperiam, eaque ipsa quae ab illo inventore veritatis architect"</p>
    <div style="margin-top:30px;font-size:13.5px;font-weight:500">Owen Hartley</div>
    <div style="font-size:12px;color:var(--muted)">Asset Portfolio Manager</div>
  </div>
  <div class="card abs" style="left:458px;top:3419px;width:284px;height:282px;padding:36px 20px 0">
    <span class="quote o">“</span>
    <div style="display:flex;justify-content:space-between;align-items:center"><span class="stars">★★★★★</span><span class="badge"></span></div>
    <p class="body-text" style="margin-top:14px;color:#3d454c;font-size:12px;line-height:22px">"Sed ut perspiciatis unde omnis iste natus error sit voluptatem accusantium laudantium, totam rem aperiam, eaque ipsa quae ab illo inventore veritatis architect"</p>
    <div style="margin-top:30px;font-size:13.5px;font-weight:500">Clara Whitmore</div>
    <div style="font-size:12px;color:var(--muted)">Senior Leasing Specialist</div>
  </div>
  <div class="card abs" style="left:776px;top:3419px;width:284px;height:282px;padding:36px 20px 0">
    <span class="quote">“</span>
    <div style="display:flex;justify-content:space-between;align-items:center"><span class="stars">★★★★★</span><span class="badge"></span></div>
    <p class="body-text" style="margin-top:14px;color:#3d454c;font-size:12px;line-height:22px">"Sed ut perspiciatis unde omnis iste natus error sit voluptatem accusantium laudantium, totam rem aperiam, eaque ipsa quae ab illo inventore veritatis architect"</p>
    <div style="margin-top:30px;font-size:13.5px;font-weight:500">Daniel Reyes</div>
    <div style="font-size:12px;color:var(--muted)">Regional Property Director</div>
  </div>
  <div class="abs" style="left:89px;top:3547px;width:24px;height:24px;border-radius:50%;background:#d5d8db;color:#fff;text-align:center;line-height:23px;font-size:14px">‹</div>
  <div class="abs" style="left:1087px;top:3547px;width:24px;height:24px;border-radius:50%;background:var(--navy);color:#fff;text-align:center;line-height:23px;font-size:14px">›</div>
  <div class="abs" style="left:571px;top:3730px;display:flex;gap:10px">
    <span style="width:7px;height:7px;border-radius:50%;background:#cfd3d6"></span><span style="width:7px;height:7px;border-radius:50%;background:var(--orange)"></span><span style="width:7px;height:7px;border-radius:50%;background:#cfd3d6"></span><span style="width:7px;height:7px;border-radius:50%;background:#cfd3d6"></span>
  </div>
</section>

<!-- contact band + footer background -->
<svg class="abs" style="left:0;top:3810px" width="1200" height="1211" viewBox="0 0 1200 1211" aria-hidden="true">
  <defs><linearGradient id="og" x1="0" y1="0" x2="0" y2="1"><stop offset="0" stop-color="#f26b40"/><stop offset="1" stop-color="#f5805a"/></linearGradient></defs>
  <polygon points="0,58 1200,0 1200,760 0,818" fill="url(#og)"/>
  <polygon points="0,790 1200,745 1200,1211 0,1211" fill="var(--navy)"/>
</svg>

<section class="abs" style="left:140px;top:3945px;width:918px;height:536px;background:#fff;border-radius:6px;box-shadow:0 10px 30px rgba(0,0,0,.1)">
  <div class="label abs" style="top:80px;left:0;width:918px;justify-content:center"><svg class="pin" viewBox="0 0 14 16"><circle cx="7" cy="6" r="5" fill="none" stroke="var(--orange)" stroke-width="2"/><path d="M7 16l-3-5h6z" fill="var(--orange)"/></svg>Contact Us</div>
  <div class="heading abs" style="top:106px;left:0;width:918px;text-align:center">Ready To Discuss Your <span class="accent">Property Goals?</span></div>
  <div class="field" style="left:121px;top:157px;width:329px"><span class="ic"><svg viewBox="0 0 14 14"><circle cx="7" cy="4.5" r="3"/><path d="M1.5 13c1-3 3-4.5 5.5-4.5s4.5 1.5 5.5 4.5"/></svg></span>First Name</div>
  <div class="field" style="left:466px;top:157px;width:331px"><span class="ic"><svg viewBox="0 0 14 14"><circle cx="7" cy="4.5" r="3"/><path d="M1.5 13c1-3 3-4.5 5.5-4.5s4.5 1.5 5.5 4.5"/></svg></span>Last Name</div>
  <div class="field" style="left:121px;top:220px;width:329px"><span class="ic"><svg viewBox="0 0 14 14"><rect x="1" y="3" width="12" height="8"/><path d="M1 3l6 5 6-5"/></svg></span>Your Email</div>
  <div class="field" style="left:466px;top:220px;width:331px"><span class="ic"><svg viewBox="0 0 14 14"><path d="M3 1.5h3l1 3-2 1.2a7 7 0 0 0 3.3 3.3L9.5 7l3 1v3c0 1-1 1.5-2 1.5C5.5 12 2 8.5 1.5 3.5c0-1 .5-2 1.5-2z"/></svg></span>Phone</div>
  <div class="field" style="left:121px;top:282px;width:676px;height:102px;align-items:flex-start;padding-top:12px"><span class="ic"><svg viewBox="0 0 14 14"><path d="M1.5 2h11v8H5l-3.5 2.5z"/></svg></span>Your Message</div>
  <div class="abs btn btn-navy" style="left:121px;top:417px;width:676px;height:47px">Submit Now <svg viewBox="0 0 12 12"><path d="M2 10L10 2M4 2h6v6" stroke="#fff" stroke-width="1.6" fill="none"/></svg></div>
</section>

<!-- footer -->
<footer>
  <div class="abs" style="left:1068px;top:4740px;width:160px;height:160px;border-radius:50%;border:22px solid rgba(255,255,255,.05)"></div>
  <div class="abs brand" style="left:143px;top:4712px">
    <span class="brand-dot"></span>
    <span class="brand-name" style="color:#fff">Varenna Group</span>
  </div>
  <p class="abs" style="left:143px;top:4770px;width:220px;font-size:12px;line-height:20px;color:#dfe4e8">Sed ut perspiciatis unde omnis iste natus error sit voluptatem accusantium dolorem.</p>
  <div class="abs" style="left:143px;top:4868px;display:flex;align-items:center;gap:8px;font-size:12px;color:#dfe4e8">Follow Us:
    <span style="width:20px;height:20px;border-radius:50%;border:1px solid #dfe4e8;margin-left:6px"></span>
    <span style="width:20px;height:20px;border-radius:50%;background:var(--orange)"></span>
    <span style="width:20px;height:20px;border-radius:50%;border:1px solid #dfe4e8"></span>
  </div>

  <div class="abs" style="left:417px;top:4708px">
    <div class="foot-h">Quick Links</div><div class="foot-bar"></div>
    <ul class="foot-list"><li>Home</li><li>Commercial / Industrial</li><li>Residential</li><li>Business Sales ⌄</li><li>About Us</li><li>Contact us</li></ul>
  </div>
  <div class="abs" style="left:651px;top:4708px">
    <div class="foot-h">Key Offerings</div><div class="foot-bar"></div>
    <ul class="foot-list"><li>Business listings</li><li>Appraisal report</li><li>What we do</li><li>Who we are</li></ul>
  </div>
  <div class="abs" style="left:838px;top:4708px;width:230px">
    <div class="foot-h">Contact Us</div><div class="foot-bar"></div>
    <div style="display:flex;gap:14px;font-size:12px;line-height:20px;color:#dfe4e8"><span style="flex:none;width:30px;height:30px;border-radius:50%;background:#33475a;display:flex;align-items:center;justify-content:center"><svg width="12" height="14" viewBox="0 0 12 14"><path d="M6 13S1.5 8 1.5 5a4.5 4.5 0 0 1 9 0C10.5 8 6 13 6 13z" fill="none" stroke="#fff" stroke-width="1.4"/><circle cx="6" cy="5" r="1.6" fill="#fff"/></svg></span>123, Lorem ipsum, dolor sit amet, adipiscing elit, 45</div>
    <div style="display:flex;gap:14px;align-items:center;margin-top:16px;font-size:12px;color:#dfe4e8"><span style="flex:none;width:30px;height:30px;border-radius:50%;background:var(--orange);display:flex;align-items:center;justify-content:center"><svg width="13" height="13" viewBox="0 0 14 14"><path d="M3 1.5h3l1 3-2 1.2a7 7 0 0 0 3.3 3.3L9.5 7l3 1v3c0 1-1 1.5-2 1.5C5.5 12 2 8.5 1.5 3.5c0-1 .5-2 1.5-2z" fill="#fff"/></svg></span>Phone: (555) 014 2298</div>
    <div style="display:flex;gap:14px;align-items:center;margin-top:16px;font-size:12px;color:#dfe4e8"><span style="flex:none;width:30px;height:30px;border-radius:50%;background:#33475a;display:flex;align-items:center;justify-content:center"><svg width="13" height="11" viewBox="0 0 13 11"><rect x=".7" y=".7" width="11.6" height="9.6" fill="none" stroke="#fff" stroke-width="1.3"/><path d="M.7 .7l5.8 5 5.8-5" fill="none" stroke="#fff" stroke-width="1.3"/></svg></span>info@varennagroup.com.au</div>
  </div>
  <div class="abs" style="left:0;top:4962px;width:1200px;height:1px;background:rgba(255,255,255,.12)"></div>
  <div class="abs" style="left:0;top:4980px;width:1200px;text-align:center;font-size:11px;color:#cfd6dc">© 2023 Varenna Business Sales. All Rights Reserved.</div>
</footer>

</body>
</html>
```